4D Cradle Glimpse Luxury Ultrasound Billboard

Design a HIGH-END, MODERN billboard for my private prenatal ultrasound studio, 4D Cradle Glimpse, located in Pace, Florida.
This billboard will be viewed by drivers traveling at highway speeds, so it must be extremely clean, simple, and readable within 6 seconds.
About My Business
4D Cradle Glimpse is a private prenatal ultrasound studio specializing in:
Highest technology 4D/HD Ultrasounds
Early Gender Determination
Pregnancy Confirmation
I have been serving families for nearly 10 years and is known for creating a memorable experience, not just an ultrasound appointment.
Design Style
I DO NOT want:
Flowers
Leaves
Swirls
Glitter
Hearts everywhere
Busy backgrounds
Generic maternity stock graphics
I DO want:
Modern
Luxury
Upscale
Clean
Professional
Eye-catching
Premium medical spa feel
Colors
Use colors from my logo:
LOGO Green ( or a deep green)
Black
White
Soft Gold accents
Images:
Incorporate my professional headshot in a clean, modern way, logo, and the ultrasound images
Text
Keep wording minimal.
Primary Headline ( OPEN TO IDEAS) :
EXAMPLES ( WOULD RATHER SOMETHING MORE CATCHY)
" ADVANCED IMAGING. UNFORGETTABLE MOMENTS"
"MEET YOUR BABY BEFORE BIRTH"
Under headline:
4D Ultrasound • Early Gender • Pregnancy Confirmation
Business Name:
4D Cradle Glimpse
Private Prenatal Ultrasound Studio
Phone Number:
850-471-5923
Important
This billboard must be readable in 5–6 seconds from a moving vehicle.
Less text is better.
The phone number and business name must be visible from a distance.
The design should feel like a premium brand that immediately tells expecting parents:
“This is where I go to see my baby.”
Files Provided
Official logo
Headshot
Ultrasound images
Don’t make this look like a medical office billboard.
Make it look like a luxury baby experience billboard. That’s what separates 4D Cradle Glimpse from hospitals, OB offices, and all the new studios popping up around you. The emotional connection is what gets moms to book. ❤️
Billboard Size - 10.6” x 36”

```html
<!DOCTYPE html>
<html lang="en">
<head>
<meta charset="utf-8">
<title>4D Cradle Glimpse – Billboard</title>
<link rel="stylesheet" href="https://fonts.googleapis.com/css2?family=Bebas+Neue&family=Alex+Brush&family=Montserrat:wght@500&display=swap">
<style>
  :root{
    --green:#3f5240;
    --green-soft:#4d5d58;
    --gold:#c49a3c;
    --gold-light:#e6c98d;
    --cream:#fdf1e6;
    --white:#ffffff;
    --ink:#111111;
    --page:#eef0f2;
  }
  *{margin:0;padding:0;box-sizing:border-box}
  html,body{width:1200px;height:1080px;overflow:hidden;background:var(--page)}
  .stage{position:relative;width:1200px;height:1080px}
  .billboard{
    position:absolute;left:30px;top:374px;
    width:1930px;height:560px;
    transform:scale(0.5907);transform-origin:0 0;
    background:var(--cream);overflow:hidden;
    font-family:"Bebas Neue",sans-serif;
  }
  .accent{position:absolute;inset:0;width:1930px;height:560px}
  .brand-panel{
    position:absolute;left:50px;top:48px;width:565px;height:277px;
    background:var(--white);border:5px solid var(--green-soft);border-radius:42px;
    box-shadow:0 10px 10px -4px rgba(60,40,80,.45);
    display:flex;flex-direction:column;align-items:center;justify-content:center;
  }
  .brand-name{
    color:var(--green);font-size:98px;line-height:.92;text-align:center;letter-spacing:1px;
  }
  .brand-rule{width:495px;height:2px;background:var(--gold);margin:14px 0 16px}
  .brand-tagline{
    font-family:"Montserrat",sans-serif;font-weight:500;font-size:22px;
    letter-spacing:1px;color:var(--green-soft);
  }
  .headline{
    position:absolute;left:658px;top:43px;color:var(--green);
    font-size:171px;line-height:.88;letter-spacing:0;font-weight:400;white-space:nowrap;
  }
  .headline-script{
    position:absolute;left:1082px;top:170px;
    font-family:"Alex Brush",cursive;color:var(--gold);
    font-size:160px;line-height:1;white-space:nowrap;
  }
  .services{
    position:absolute;left:98px;top:381px;color:var(--gold);
    font-size:67px;line-height:1;letter-spacing:0;white-space:nowrap;
  }
  .contact{
    position:absolute;left:110px;top:454px;
    display:flex;align-items:center;gap:18px;
    color:var(--green);font-size:88px;line-height:1;white-space:nowrap;
  }
  .contact .rule{width:100px;height:4px;background:var(--gold)}
  .contact .divider{color:var(--gold);margin:0 6px}
  .tablet{
    position:absolute;left:1387px;top:298px;width:153px;height:227px;
    background:var(--ink);border-radius:12px;padding:38px 10px 28px;
    box-shadow:0 8px 10px rgba(0,0,0,.35);
  }
  .tablet .screen{
    width:100%;height:100%;
    background:linear-gradient(135deg,#5a2418,#b5644c 45%,#7a3323 70%,#2a0c07);
  }
  .portrait{
    position:absolute;left:1570px;top:30px;width:360px;height:530px;
    background:linear-gradient(180deg,#d7c3a3 0%,#c9a37a 30%,#3e5a3e 62%,#2c3d2c 100%);
    border-radius:160px 160px 0 0;
  }
</style>
</head>
<body>
<div class="stage">
  <section class="billboard">
    <svg class="accent" viewBox="0 0 1930 560" aria-hidden="true">
      <defs>
        <linearGradient id="goldLeft" x1="0" y1="0" x2="0" y2="1">
          <stop offset="0" stop-color="#c49a3c"/>
          <stop offset="1" stop-color="#f0dcb4"/>
        </linearGradient>
        <linearGradient id="goldRight" x1="0" y1="0" x2="1" y2="1">
          <stop offset="0" stop-color="#c49a3c"/>
          <stop offset="1" stop-color="#f3dfba"/>
        </linearGradient>
      </defs>
      <polygon points="0,0 170,0 0,500" fill="url(#goldLeft)"/>
      <polygon points="1600,0 1930,0 1930,560 1420,560" fill="url(#goldRight)"/>
      <polygon points="1640,0 1680,0 1500,560 1460,560" fill="#e9cf9c" opacity=".6"/>
    </svg>

    <div class="brand-panel">
      <div class="brand-name">4D<br>Cradle Glimpse</div>
      <div class="brand-rule"></div>
      <div class="brand-tagline">PRENATAL ULTRASOUND STUDIO</div>
    </div>

    <h1 class="headline">MEET YOUR BABY<br>BEFORE</h1>
    <span class="headline-script">Birth</span>

    <p class="services">4D ULTRASOUND • EARLY GENDER • PREGNANCY CONFIRMATION</p>

    <p class="contact">
      <span class="rule"></span>
      <span>850-471-5923<span class="divider">|</span>4DCRADLEGLIMPSE.COM</span>
      <span class="rule"></span>
    </p>

    <div class="tablet">
      <div class="screen" role="img" aria-label="4D ultrasound image of twin babies face to face"></div>
    </div>

    <div class="portrait" role="img" aria-label="Professional headshot of the studio owner in green scrubs holding an ultrasound probe"></div>
  </section>
</div>
</body>
</html>
```